New business card for a regional office of a US M&A company

We need business card for a finance company, office based in Hong Kong , our Head office is in US, our business is to Merge and acquires companies , the new office will be a regional office for the Asia Pacific region. We want to use the head office logo as attached ( but don't have to be exactly the same, can be a variation to it) as a base and then add Asia Pacific alongside the logo.
We would prefer to have be bilingual Eng + Chinese, although we don't really have Chinese company name .

Industry/Entity Type

Business

Contact Information for Business Card

Clara Jo Tsang
 

VP,
APAC M&A Operations
ORIN VANTAGE Asia Pacific Limited
 
Unit 1407, K18
18 Tai Lok Shan Road, 
Hong Kong 
 
M: +852 6038 1742
T : +852 2836 4100
F : +852 2836 4177
VOIP: 4158
 
cjtsang@orinvantage.com

Font styles to use
Serif
Sans Serif

Colors

Designer to choose colors to be used in the design.

Requirements
Must have
• APAC Office

```html
<!DOCTYPE html>
<html lang="en">
<head>
<meta charset="utf-8">
<title>Orin Vantage Asia Pacific – Business Card</title>
<link rel="stylesheet" href="https://fonts.googleapis.com/css2?family=Ubuntu:wght@400;500;700&family=Ubuntu+Condensed&display=swap">
<style>
  :root {
    --page: #e8e8e8;
    --navy: #0e2740;
    --cyan: #1fa3c9;
    --cyan-deep: #1b8fb4;
    --silver: #d9dde0;
    --silver-dark: #a9b0b6;
    --white: #ffffff;
    --ink: #0e2740;
  }
  * { margin: 0; padding: 0; box-sizing: border-box; }
  html, body { width: 1200px; height: 576px; overflow: hidden; }
  body {
    background: var(--page);
    font-family: "Ubuntu", sans-serif;
    position: relative;
  }
  .card {
    position: absolute;
    top: 138px;
    width: 484px;
    height: 294px;
    border-radius: 12px;
    background: var(--navy);
    overflow: hidden;
  }
  .card--front { left: 82px; }
  .card--back { left: 602px; }

  /* Front */
  .front-stripe {
    position: absolute; left: 0; right: 0; bottom: 0; height: 8px;
    background: var(--cyan);
  }
  .front-mark {
    position: absolute; left: 50%; top: 86px;
    width: 34px; height: 34px; margin-left: -17px;
    border: 5px solid var(--white);
  }
  .front-brand {
    position: absolute; left: 0; right: 0; top: 160px;
    text-align: center;
    font-weight: 700; font-size: 37px; letter-spacing: 1px;
    color: var(--cyan);
  }

  /* Back */
  .wave { position: absolute; left: 0; top: 0; width: 484px; height: 294px; }
  .holder { position: absolute; left: 18px; top: 28px; }
  .holder__name {
    font-family: "Ubuntu Condensed", sans-serif;
    font-size: 20px; color: var(--cyan); line-height: 1.2;
  }
  .holder__title {
    margin-top: 6px; font-size: 11.5px; line-height: 14px; color: var(--white);
  }
  .brand { position: absolute; right: 26px; top: 36px; text-align: right; }
  .brand__name {
    font-weight: 700; font-size: 25px; letter-spacing: 0.5px; color: var(--cyan); line-height: 1;
  }
  .brand__web {
    margin-top: 5px; font-size: 8.5px; letter-spacing: 3.2px; color: var(--white);
  }
  .company {
    position: absolute; left: 18px; top: 140px;
    font-weight: 500; font-size: 13px; color: var(--cyan);
  }
  .contacts { position: absolute; left: 18px; top: 164px; list-style: none; }
  .contacts li {
    display: flex; align-items: center; gap: 9px;
    font-size: 11.5px; line-height: 15px; color: var(--white);
  }
  .contacts svg { width: 9px; height: 9px; fill: var(--cyan); flex: none; }
  .contacts .label { color: var(--cyan); margin-left: 4px; }
  .address {
    position: absolute; right: 21px; top: 227px;
    text-align: right; font-size: 11.5px; line-height: 14.5px; color: var(--ink);
  }
</style>
</head>
<body>

<section class="card card--front" aria-label="Card front">
  <div class="front-mark"></div>
  <div class="front-brand">ORIN VANTAGE</div>
  <div class="front-stripe"></div>
</section>

<section class="card card--back" aria-label="Card back">
  <svg class="wave" viewBox="0 0 484 294" aria-hidden="true">
    <defs>
      <linearGradient id="silverBand" x1="0" y1="0" x2="1" y2="0">
        <stop offset="0" stop-color="#bfc5ca"/>
        <stop offset="0.5" stop-color="#eef0f2"/>
        <stop offset="1" stop-color="#c9ced2"/>
      </linearGradient>
    </defs>
    <path d="M0,240 C70,262 160,282 250,262 C340,242 400,178 484,160 L484,170 C410,190 345,255 255,276 C165,296 70,276 0,256 Z" fill="url(#silverBand)"/>
    <path d="M0,262 C80,286 180,296 262,276 C350,252 412,196 484,178 L484,294 L0,294 Z" fill="var(--cyan)"/>
    <path d="M40,268 C110,290 190,290 262,276 C200,298 110,296 40,268 Z" fill="url(#silverBand)" opacity="0.9"/>
  </svg>

  <div class="holder">
    <div class="holder__name">Clara Jo Tsang</div>
    <div class="holder__title">Vice President,<br>APAC M&amp;A Operations</div>
  </div>

  <div class="brand">
    <div class="brand__name">ORIN VANTAGE</div>
    <div class="brand__web">www.orinvantage.com</div>
  </div>

  <div class="company">Orin Vantage Asia Pacific Limited</div>

  <ul class="contacts">
    <li><svg viewBox="0 0 10 10"><rect x="2" y="0" width="6" height="10" rx="1"/></svg>+852 6038 1742</li>
    <li><svg viewBox="0 0 10 10"><path d="M0,3 Q5,-1 10,3 L8,5 L6,3.5 L4,3.5 L2,5 Z M1,6 L9,6 L9,10 L1,10 Z"/></svg>+852 2836 4100</li>
    <li><svg viewBox="0 0 10 10"><rect x="2" y="0" width="6" height="3"/><rect x="0" y="4" width="10" height="4"/><rect x="2" y="8" width="6" height="2"/></svg>+852 2836 4177,<span class="label">VOIP:</span> 4158</li>
    <li><svg viewBox="0 0 10 10"><path d="M0,2 L10,2 L5,6 Z M0,3.5 L5,7.5 L10,3.5 L10,8 L0,8 Z"/></svg>cjtsang@orinvantage.com</li>
  </ul>

  <div class="address">Unit 1407, K18<br>18 Tai Lok Shan<br>Road, Hong Kong</div>
</section>

</body>
</html>
```